New Corporate Email Signature with Custom GIF KAV Electric LLC & KAV Fire & Security

Project Overview
KAV Electric LLC and KAV Fire & Security are seeking a professional, polished, and technically robust corporate email signature design. The project has two integrated deliverables:
A custom animated GIF representing both sides of our business
A complete corporate email signature layout designed for real-world compatibility (Gmail, Outlook, iOS, Android)
Our brand aesthetic is corporate, conservative, and clean. We value clarity, trust, professionalism, and subtle creativity β€” nothing overly flashy or cartoonish.
This design will be used across the entire company and must be visually aligned with our brand while remaining technically dependable.

PART 1 β€” Animated GIF Requirements
The GIF will be the core visual anchor of the new signature.
It must be clean, smooth, subtle, and optimized for email use.
βš™ Technical Requirements
Max file size: 150–200 KB (smaller is better)
Dimensions: approx 300px width (flexible, but must look good small)
Looping: continuous loop
Style: professional, minimalistic transitions

No rapid flashing or harsh animations
Must export cleanly into a format email clients accept

🎞 GIF Animation Sequence
Phase 1 β€” KAV Electric (KE)
Use the yellow β€œKE” avatar logo (provided).
Animation flow:
KE avatar appears
Full name β€œKAV Electric LLC” slides in, fades in, or otherwise appears smoothly
A scrolling or cycling list of service offerings displays:
EV Charging Stations
Generator & Transformers
Testing & Troubleshooting
LED Lighting Upgrades
After the list is shown, the entire KE segment fades out

Phase 2 β€” KAV Fire & Security (KF)
Use the red β€œKF” avatar logo (provided).
Animation flow mirrors Phase 1:
KF avatar appears
Full name β€œKAV Fire & Security” slides/fades in
Scrolling or cycling list of services displays:
Fire Alarm Upgrades
BQTL 48 Test & Inspect
Security Surveillance Systems
Access Control Systems
Data & Fiber Optic Cabling
Fade out β†’ loop back to KE
Creative Direction

Designers are encouraged to use:
Clean transitions
Soft fades
Professional typography
Modern minimalism
Consistent brand colors
High clarity at small sizes

Avoid:
Busy motion
Hard flashes
Excessive text overlays
Overly long transitions

The goal: a smooth, corporate-grade rotation that fits seamlessly into an email signature.

PART 2 β€” Corporate Email Signature Design

The signature must be visually appealing, brand-aligned, and structurally bulletproof across all major email systems.
πŸ“ Required Elements
πŸ‘€ Left Side Content
Circular headshot (we will supply final photos)
Social media icons with embedded URLs:
plain circle
plain circle
plain circle Business Profile
plain circle

Icons should be clean, modern, and in alignment with brand colors
πŸ“„ Right Side Content
Name
Title
KAV Electric LLC / KAV Fire & Security (depending on user)
Phone number
Email address
License# 52804
Physical office address: 384 Pembrook St, Westwood NJ 07912

Small CTA for newsletter signup (button or micro-banner)

🏒 Branding Assets Provided

You will receive:
KE avatar logo
KF avatar logo
Full-name KE logo
Full-name KF logo

These should be incorporated naturally and professionally.

Design Requirements

Conservative corporate styling

Clean typography

Balanced use of white space

Professional hierarchy

Light and dark mode compatibility preferred

Layout should not rely on one large image

All images should export cleanly for hosting on servers/CDN

Avoid overly tall signatures

The final signature must present as modern, trustworthy, and technically reliable across platforms.

πŸ§ͺ Compatibility Requirements

The signature must display correctly in:

Gmail (web and mobile)

Outlook (desktop & online)

Apple Mail

iPhone Mail

Android mail apps

Designers must avoid DIV-based layouts and instead propose a layout that can be implemented using table-based HTML, which is the industry standard for email compatibility.

You do not need to build the HTML β€” only supply the final layered design (PSD/AI/Figma) plus a clear structural layout that can be converted to HTML later.

πŸ“¦ Deliverables
1. Animated GIF

Final optimized GIF

Source file (After Effects, Photoshop, or equivalent)

Export guidelines so we can reproduce future versions

2. Email Signature Design

Full static design mockup

Modular layout for each employee

Icon set for social media

Newsletter CTA element

Clear spacing, alignment, and typography specifications

All source files (PSD, AI, Figma, etc.)

🧭 Creative Guidance Summary

We want:
βœ” Modern
βœ” Corporate
βœ” Minimalistic
βœ” Professional
βœ” Clean motion
βœ” Consistent branding
βœ” Email-safe elements

We do not want:
✘ Flashy marketing look
✘ Overly colorful or playful styles
✘ Hard-to-read fonts
✘ Heavy animation
✘ Oversized signatures

πŸ›  Tools & Format Flexibility

We allow full creative freedom regarding:

Animation style

Typography choices

Structuring of the two-column layout

How the service lists scroll or cycle

As long as the end result is clean, brand-aligned, professional, and email-compatible.

πŸ’¬ Final Note to Designers

We encourage creativity within the boundaries of corporate professionalism.
This signature will represent our company every time an email is sent β€” it must communicate trust, clarity, expertise, and brand strength.

```html
<!DOCTYPE html>
<html lang="en">
<head>
<meta charset="utf-8">
<title>KAV Electric LLC – Email Signature</title>
<link rel="stylesheet" href="https://fonts.googleapis.com/css2?family=Inter:wght@400;500;600;700&family=Open+Sans:wght@600&display=swap">
<style>
  :root {
    --bg: #fafafa;
    --gold: #dbb42c;
    --ink: #2e2e2e;
    --muted: #7a7a7a;
    --rule: #9c9c9c;
    --cta-dark: #16191d;
    --cta-mid: #2a3440;
    --photo-light: #e9e6ea;
    --photo-dark: #3c4452;
    --white: #ffffff;
  }
  * { margin: 0; padding: 0; box-sizing: border-box; }
  html, body {
    width: 1200px;
    height: 424px;
    overflow: hidden;
    background: var(--bg);
  }
  .signature {
    position: relative;
    width: 1200px;
    height: 424px;
    font-family: "Inter", Arial, sans-serif;
    color: var(--muted);
  }
  .headshot {
    position: absolute;
    left: 71px;
    top: 49px;
    width: 204px;
    height: 208px;
    border-radius: 50%;
    border: 3px solid var(--gold);
    background: radial-gradient(circle at 50% 38%, var(--photo-light) 0 45%, #c9c3c6 60%, var(--photo-dark) 100%);
  }
  .details {
    position: absolute;
    left: 311px;
    top: 35px;
  }
  .name {
    font-size: 30px;
    font-weight: 700;
    color: var(--muted);
    line-height: 38px;
  }
  .title {
    font-size: 21px;
    font-weight: 500;
    color: var(--ink);
    line-height: 28px;
  }
  .company {
    font-size: 20px;
    font-weight: 600;
    line-height: 28px;
    margin-top: 19px;
    color: var(--gold);
  }
  .contact {
    list-style: none;
    margin-top: 17px;
    font-size: 20px;
    line-height: 28px;
  }
  .contact li { margin-bottom: 10px; }
  .contact li:nth-child(n+3) { margin-bottom: 8px; }
  .contact .label-accent { color: var(--gold); margin-right: 6px; }
  .contact .label { color: var(--ink); font-weight: 500; margin-right: 4px; }
  .newsletter-cta {
    position: absolute;
    left: 918px;
    top: 243px;
    width: 256px;
    height: 56px;
    border-radius: 6px;
    background: linear-gradient(100deg, var(--cta-dark) 0%, var(--cta-mid) 55%, var(--cta-dark) 100%);
    display: flex;
    align-items: center;
    justify-content: center;
    font-family: "Open Sans", Arial, sans-serif;
    font-weight: 600;
    font-size: 20px;
    color: var(--white);
    text-decoration: none;
  }
  .divider {
    position: absolute;
    left: 15px;
    top: 317px;
    width: 1172px;
    height: 1px;
    background: var(--rule);
  }
  .social-links {
    position: absolute;
    left: 1034px;
    top: 365px;
    display: flex;
    gap: 13px;
    list-style: none;
  }
  .social-links a {
    display: block;
    width: 24px;
    height: 24px;
    border-radius: 50%;
    background: var(--gold);
  }
</style>
</head>
<body>
  <div class="signature">
    <div class="headshot" role="img" aria-label="Circular headshot photo of Daniel Reyes"></div>

    <div class="details">
      <p class="name">Daniel Reyes</p>
      <p class="title">Project Manager</p>
      <p class="company">KAV Electric LLC</p>
      <ul class="contact">
        <li><span class="label-accent">P :</span>555-218-4093</li>
        <li><span class="label-accent">E :</span> daniel.reyes@kavelectric.com</li>
        <li><span class="label">License</span># 52804</li>
        <li><span class="label">Office</span>384 Pembrook St, Millbrook PA 07912</li>
      </ul>
    </div>

    <a class="newsletter-cta" href="#">Join Our Newsletter</a>

    <div class="divider"></div>

    <ul class="social-links">
      <li><a href="#" aria-label="Photo sharing profile"></a></li>
      <li><a href="#" aria-label="Social network profile"></a></li>
      <li><a href="#" aria-label="Professional network profile"></a></li>
      <li><a href="#" aria-label="Business listing profile"></a></li>
    </ul>
  </div>
</body>
</html>
```